Business Card Design for company

We want new business cards. We'd like something different-- yet still highly professional. Our tagline is Providing leadership, delivering success. Stock photos are ok, as long as they are relevant and look upscale.

Target Market(s)

Architecture/Business Management Consulting/Engineering Consulting

Contact Information for Business Card

dark gray background with pops of blue might be good, but you tell me. You're the designers. Rounded corners might be nice, but again, you tell me.

Font styles to use
Serif
Sans Serif

Colors
3276b5
5c5c5c
9d9d9d
fbfbfb

Requirements
Nice to have
• Something different, but still very professional.

```html
<!DOCTYPE html>
<html lang="en">
<head>
<meta charset="utf-8">
<title>Halden Advisory — Business Card</title>
<link href="https://fonts.googleapis.com/css2?family=Montserrat:wght@400;500;600;700&display=swap" rel="stylesheet">
<style>
  :root {
    --stage: #1b1b1c;
    --card: #343536;
    --card-back: #2f3031;
    --pattern: #3a3b3c;
    --blue: #3276b5;
    --grey: #5c5c5c;
    --muted: #9d9d9d;
    --white: #fbfbfb;
  }
  * { box-sizing: border-box; margin: 0; padding: 0; }
  html, body {
    width: 1200px; height: 900px; overflow: hidden;
    background: var(--stage);
    font-family: "Montserrat", sans-serif;
  }
  .stage {
    width: 1200px; height: 900px;
    display: flex; flex-direction: column; align-items: center; justify-content: center;
    gap: 36px;
  }
  .card {
    position: relative;
    width: 700px; height: 400px;
    border-radius: 6px;
    overflow: hidden;
    box-shadow: 0 12px 30px rgba(0,0,0,.55);
  }

  /* Back face */
  .card--back { background: var(--card-back); display: flex; align-items: center; justify-content: center; }
  .card__pattern { position: absolute; inset: 0; background: linear-gradient(135deg, var(--pattern), var(--card-back)); }
  .card__mark { position: relative; color: var(--blue); font-weight: 600; font-size: 40px; letter-spacing: 1px; }

  /* Front face */
  .card--front { background: var(--card); }
  .front__claim {
    position: absolute; top: 30px; left: 0; right: 0; text-align: center;
    color: var(--muted); font-size: 13px; font-weight: 500; letter-spacing: 1px;
  }
  .front__brand {
    position: absolute; left: 50px; top: 150px; width: 300px;
    color: var(--blue); font-weight: 600; font-size: 46px; line-height: 1.05;
  }
  .front__divider {
    position: absolute; left: 370px; top: 118px; width: 2px; height: 190px;
    background: var(--white);
  }
  .front__details { position: absolute; left: 400px; top: 118px; color: var(--white); }
  .person__name { color: var(--blue); font-size: 26px; font-weight: 500; letter-spacing: 1.5px; text-transform: uppercase; }
  .person__role { font-size: 15px; margin-top: 2px; }
  .address { font-size: 15px; line-height: 1.45; margin-top: 18px; letter-spacing: .5px; }
  .contacts { list-style: none; margin-top: 12px; font-size: 15px; letter-spacing: .5px; }
  .contacts li { display: flex; align-items: center; gap: 10px; line-height: 1.6; }
  .contacts svg { width: 12px; height: 12px; flex: none; }
  .front__tagline {
    position: absolute; bottom: 30px; left: 0; right: 0; text-align: center;
    color: var(--white); font-size: 18px; font-weight: 600; letter-spacing: .5px;
  }
</style>
</head>
<body>
<main class="stage">
  <section class="card card--back" aria-label="Card back">
    <div class="card__pattern" role="img" aria-label="Embossed repeating company name pattern"></div>
    <span class="card__mark">Halden Advisory</span>
  </section>

  <section class="card card--front" aria-label="Card front">
    <p class="front__claim">Trusted Construction Management Advisor since 1999.</p>
    <div class="front__brand">Halden Advisory</div>
    <div class="front__divider"></div>
    <div class="front__details">
      <h1 class="person__name">Daniel Hartley</h1>
      <p class="person__role">Director</p>
      <p class="address">58 Harbour Lane,<br>Wellington, NZ, 6011</p>
      <ul class="contacts">
        <li>
          <svg viewBox="0 0 12 12" aria-hidden="true"><path d="M2.5 1h2l1 2.5-1.3 1a6 6 0 0 0 3.3 3.3l1-1.3L11 7.5v2A1.5 1.5 0 0 1 9.5 11 8.5 8.5 0 0 1 1 2.5 1.5 1.5 0 0 1 2.5 1z" fill="var(--blue)"/></svg>
          (555) 013-2048
        </li>
        <li>
          <svg viewBox="0 0 12 12" aria-hidden="true"><rect x="1" y="2.5" width="10" height="7" fill="none" stroke="var(--blue)" stroke-width="1.2"/><path d="M1 2.5l5 4 5-4" fill="none" stroke="var(--blue)" stroke-width="1.2"/></svg>
          hello@haldenadvisory.com
        </li>
        <li>
          <svg viewBox="0 0 12 12" aria-hidden="true"><circle cx="6" cy="6" r="5" fill="none" stroke="var(--blue)" stroke-width="1.1"/><ellipse cx="6" cy="6" rx="2.2" ry="5" fill="none" stroke="var(--blue)" stroke-width="1"/><path d="M1 6h10" stroke="var(--blue)" stroke-width="1"/></svg>
          www.haldenadvisory.com
        </li>
      </ul>
    </div>
    <p class="front__tagline">Providing Leadership, Delivering Success</p>
  </section>
</main>
</body>
</html>
```